Vodka Bottle Label - Luma Vodka

I need a bottle label for a vodka I'd like to make called Luma Vodka.
I would like a label that looks elegant and fresh. I would like some mountains and colours to be red and white. Open to other colours being added but not too colourful. "Luma" means fresh, dawn in polish, i would like if mountains or something extra was added to the label too. I would like the Luma Vodka name not to be too small.
The vodka is made in australia and is 37%.

I would love to have a little bit of gold colour in the label!

I will provide the back label words when completing my decision.

i'd like to make it more simple and less european looking. More australian.

I saw a bottle like this and i did like the concept.

https://www.tallgumcellars.com.au/spirits/qrnt-vodka-range?srsltid=ZtqWXkelmaHuP31-ra-m7s92xudhfew_pT8eWnGBbRTxLsb3hTyQsdGaqYt

Target Market(s)

Vodka Drinkers

Industry/Entity Type

Alcohol

Colors
EB3D1F
EC4F4E
F09395
F8D3D4
FCEDEE

Requirements
Must have
• red and white colours incorporated, mountains or freshness on it.
Nice to have
• Fresh and clean look. Classy

```html
<!DOCTYPE html>
<html lang="en">
<head>
<meta charset="utf-8">
<title>Luma Vodka – Label</title>
<link href="https://fonts.googleapis.com/css2?family=Open+Sans:wght@400;500&display=swap" rel="stylesheet">
<style>
  :root {
    --backdrop: #eef1f4;
    --label-top: #fcfdfd;
    --label-side: #eceff2;
    --label-edge: #dfe4e8;
    --wordmark: #8f9296;
    --ink: #1f2326;
    --dawn-red: #eb3d1f;
    --dawn-coral: #ec4f4e;
    --dawn-rose: #f09395;
    --dawn-blush: #f8d3d4;
    --dawn-mist: #fcedee;
    --gold: #c9a24a;
  }
  html, body {
    margin: 0;
    padding: 0;
    width: 940px;
    height: 1200px;
    overflow: hidden;
    background: var(--backdrop);
  }
  .canvas {
    position: relative;
    width: 940px;
    height: 1200px;
    font-family: "Open Sans", Arial, sans-serif;
  }
  .label {
    position: absolute;
    left: 200px;
    top: 60px;
    width: 540px;
    height: 1080px;
    border-radius: 44px;
    overflow: hidden;
    background: linear-gradient(90deg, var(--label-side) 0%, var(--label-top) 22%, var(--label-top) 78%, var(--label-side) 100%);
    box-shadow: inset 0 0 0 1px var(--label-edge), 0 24px 40px -20px rgba(40, 60, 80, 0.25);
  }
  .wordmark {
    position: absolute;
    left: 270px;
    top: 330px;
    margin: 0;
    transform: translate(-50%, -50%) rotate(-90deg);
    font-size: 120px;
    font-weight: 400;
    letter-spacing: 4px;
    color: var(--wordmark);
    line-height: 1;
    white-space: nowrap;
  }
  .product-type {
    position: absolute;
    left: 0;
    right: 0;
    top: 540px;
    margin: 0;
    text-align: center;
    font-size: 30px;
    font-weight: 400;
    letter-spacing: 1px;
    color: var(--ink);
  }
  .gold-rule {
    position: absolute;
    left: 220px;
    top: 596px;
    width: 100px;
    height: 2px;
    background: var(--gold);
  }
  .swirl-artwork {
    position: absolute;
    left: 70px;
    top: 630px;
    width: 400px;
    height: 260px;
    border-radius: 130px;
    background:
      radial-gradient(circle at 55% 40%, var(--dawn-blush) 0%, rgba(248, 211, 212, 0) 60%),
      radial-gradient(circle at 35% 70%, var(--dawn-rose) 0%, rgba(240, 147, 149, 0) 45%),
      var(--dawn-mist);
    opacity: 0.7;
  }
  .ridge-line {
    position: absolute;
    left: 0;
    top: 900px;
    width: 540px;
    height: 90px;
  }
  .origin-details {
    position: absolute;
    left: 0;
    right: 0;
    top: 1000px;
    text-align: center;
    font-size: 22px;
    line-height: 1.25;
    color: var(--ink);
  }
  .origin-details p { margin: 0; }
</style>
</head>
<body>
  <main class="canvas">
    <section class="label">
      <h1 class="wordmark">LUMA</h1>
      <p class="product-type">VODKA</p>
      <div class="gold-rule"></div>
      <div class="swirl-artwork" role="img" aria-label="Soft brushed swirl artwork in dawn tones"></div>
      <svg class="ridge-line" viewBox="0 0 540 90" aria-hidden="true">
        <polyline points="40,80 130,40 180,60 270,10 340,55 390,35 500,80" fill="none" stroke="var(--dawn-red)" stroke-width="3" stroke-linejoin="round"/>
        <line x1="40" y1="86" x2="500" y2="86" stroke="var(--gold)" stroke-width="2"/>
      </svg>
      <div class="origin-details">
        <p>Made In Australia</p>
        <p>ALC. 37%VOL.</p>
      </div>
    </section>
  </main>
</body>
</html>
```